New business card/stationary for a consulting company

I am looking for a clean and very professional looking business card for my consulting company as well as corresponding stationary. I am uploading our logo. I like simple and powerful for the feel. No graphics but I am open on everything else. Below is my contact information but would like the final to be in a version I can add my employees information into and print. Thank you.

Daniel Whitcombe
dan@ferncliffadvisory.com
2870 North 9th Avenue, Summit Floor, Elm Ridge, Illinois 60531
www.ferncliffadvisory.com

Industry/Entity Type

Consulting

Contact Information for Business Card

Daniel Whitcombe
dan@ferncliffadvisory.com
www.ferncliffadvisory.com

Font styles to use
Serif
Sans Serif

Requirements
Must have
• Our logo and the business card details.
Nice to have
• our website www.ferncliffadvisory.com

```html
<!DOCTYPE html>
<html lang="en">
<head>
<meta charset="utf-8">
<title>Ferncliff Advisory – Business Card</title>
<link rel="stylesheet" href="https://fonts.googleapis.com/css2?family=Tenor+Sans&family=Roboto:wght@400;700&display=swap">
<style>
  :root {
    --backdrop: #d9dcdf;
    --card: #eef0f2;
    --card-edge: #d3d6da;
    --navy: #1c1a4c;
    --ink: #3b3b45;
    --ink-strong: #2c2c34;
    --gold: #b8ab8a;
    --email: #e4e4ee;
  }
  * { margin: 0; padding: 0; box-sizing: border-box; }
  html, body {
    width: 1200px;
    height: 969px;
    overflow: hidden;
    background: var(--backdrop);
  }
  .canvas {
    position: relative;
    width: 1200px;
    height: 969px;
  }
  .card {
    position: absolute;
    left: 100px;
    top: 202px;
    width: 1000px;
    height: 564px;
    background: var(--card);
    border: 1px solid var(--card-edge);
    border-radius: 6px;
    overflow: hidden;
  }
  .brand {
    position: absolute;
    left: 72px;
    top: 150px;
    display: flex;
    align-items: center;
    gap: 18px;
  }
  .brand-square {
    width: 26px;
    height: 26px;
    background: var(--navy);
  }
  .brand-name {
    font-family: "Tenor Sans", sans-serif;
    font-size: 38px;
    letter-spacing: 1.5px;
    color: var(--navy);
    text-transform: uppercase;
    white-space: nowrap;
  }
  .address {
    position: absolute;
    left: 74px;
    top: 372px;
    font-family: "Roboto", sans-serif;
    font-size: 23px;
    line-height: 31px;
    color: var(--ink);
  }
  .address .website {
    font-weight: 700;
    color: var(--ink-strong);
    text-transform: uppercase;
    margin-top: 2px;
  }
  .name-band {
    position: absolute;
    left: 567px;
    top: 381px;
    width: 433px;
    height: 105px;
    background: var(--navy);
    padding: 16px 40px 0 36px;
  }
  .name-band::after {
    content: "";
    position: absolute;
    left: 0;
    right: 0;
    bottom: -9px;
    height: 3px;
    background: var(--navy);
  }
  .person-name {
    font-family: "Tenor Sans", sans-serif;
    font-size: 27px;
    letter-spacing: 2px;
    color: var(--gold);
    text-transform: uppercase;
    white-space: nowrap;
  }
  .person-email {
    font-family: "Roboto", sans-serif;
    font-size: 22px;
    color: var(--email);
    text-align: right;
    margin-top: 4px;
    white-space: nowrap;
  }
</style>
</head>
<body>
<main class="canvas">
  <section class="card">
    <div class="brand">
      <span class="brand-square"></span>
      <span class="brand-name">Ferncliff Advisory</span>
    </div>
    <address class="address">
      <div>2870 North 9th Avenue</div>
      <div>Summit Floor, Elm Ridge</div>
      <div>Illinois 60531</div>
      <div class="website">ferncliffadvisory.com</div>
    </address>
    <div class="name-band">
      <div class="person-name">Daniel Whitcombe</div>
      <div class="person-email">dan@ferncliffadvisory.com</div>
    </div>
  </section>
</main>
</body>
</html>
```